Business card for my new company (Accounting firm)

I need a business card for my new business Brightwell Advisory and Ledger SA. Our services are accounting, tax, audit and financial management. Our customers are small companies, start-ups and new companies. The final design has to show financial security, trust and growth. Please find our logo attached to the business card. Text for the business card: Brightwell Advisory and Ledger SA Tomas Varenholt Director and Founder Certified Accountant Tel. 022 418 57 34 tv@clairevalconseil.ch www.clairevalconseil.ch Rue des Vergières 27 1201 Geneva
Target Market(s)
Our customers are small companies, start-ups and new companies.
Industry/Entity Type
Finance And Accounting
Contact Information for Business Card
Claireval Conseil et Comptes SA
Tomas Varenholt
Directeur et Fondateur
Expert-comptable diplômé
Tél. 022 418 57 34
tv@clairevalconseil.ch
www.clairevalconseil.ch
Rue des Vergières 27
1201 Genève

```html
<!DOCTYPE html>
<html lang="fr">
<head>
<meta charset="utf-8">
<title>Claireval Conseil et Comptes SA – Carte de visite</title>
<link rel="stylesheet" href="https://fonts.googleapis.com/css2?family=Roboto:wght@400;500;700&display=swap">
<style>
  :root {
    --backdrop: #3b3b3d;
    --card: #1f2023;
    --card-edge: #17181a;
    --accent: #2b93d9;
    --accent-light: #4fb3ee;
    --text: #f1f3f5;
    --text-soft: #c9ccd1;
    --emboss: #2c2d31;
  }
  * { box-sizing: border-box; margin: 0; padding: 0; }
  html, body { width: 799px; height: 1200px; overflow: hidden; }
  body {
    background: var(--backdrop);
    font-family: "Roboto", Arial, sans-serif;
    position: relative;
  }
  .card {
    position: absolute;
    left: 90px;
    width: 620px;
    height: 380px;
    background: var(--card);
    border-radius: 4px;
    box-shadow: 0 14px 30px rgba(0,0,0,.45);
    overflow: hidden;
  }
  .card--front { top: 110px; }
  .card--back { top: 710px; }
  .card__band {
    position: absolute;
    left: 0; right: 0; bottom: 0;
    height: 20px;
    background: linear-gradient(var(--accent-light), var(--accent));
  }
  .brand {
    display: flex;
    align-items: center;
    gap: 14px;
    font-family: "Roboto", Arial, sans-serif;
    font-weight: 700;
    text-transform: uppercase;
  }
  .brand__mark { width: 34px; height: 34px; flex: none; }
  .brand__name { font-size: 46px; letter-spacing: 3px; line-height: 1; }
  .brand__sub { font-size: 13px; letter-spacing: 3.4px; margin-top: 6px; }
  .card--front .brand {
    position: absolute;
    left: 50%; top: 46%;
    transform: translate(-50%, -50%);
    color: var(--emboss);
  }
  .card--front .brand__mark { background: var(--emboss); }
  .card--back .brand {
    position: absolute;
    right: 34px; top: 150px;
    color: var(--text);
  }
  .card--back .brand__name { font-size: 38px; }
  .card--back .brand__sub { font-size: 11px; letter-spacing: 2.8px; }
  .card--back .brand__mark { background: var(--accent); width: 28px; height: 28px; }
  .contact {
    position: absolute;
    left: 32px; top: 190px;
    color: var(--text);
  }
  .contact__name {
    font-weight: 700;
    font-size: 22px;
    color: var(--accent);
    margin-bottom: 6px;
  }
  .contact__role { font-size: 13px; color: var(--text-soft); line-height: 1.35; }
  .contact__lines { margin-top: 12px; font-size: 14px; line-height: 1.75; }
  .contact__row { display: flex; align-items: center; gap: 16px; }
  .contact__item { display: inline-flex; align-items: center; gap: 6px; }
  .icon { width: 12px; height: 12px; fill: var(--accent); flex: none; }
</style>
</head>
<body>
  <section class="card card--front" aria-label="Recto">
    <div class="brand">
      <span class="brand__mark"></span>
      <div>
        <div class="brand__name">Claireval</div>
        <div class="brand__sub">Conseil et Comptes</div>
      </div>
    </div>
    <div class="card__band"></div>
  </section>

  <section class="card card--back" aria-label="Verso">
    <div class="contact">
      <div class="contact__name">Tomas Varenholt</div>
      <div class="contact__role">Directeur et Fondateur<br>Expert-comptable diplômé</div>
      <div class="contact__lines">
        <div class="contact__row">
          <span class="contact__item">
            <svg class="icon" viewBox="0 0 24 24"><path d="M6.6 10.8a15 15 0 0 0 6.6 6.6l2.2-2.2a1 1 0 0 1 1-.25 11.4 11.4 0 0 0 3.6.57 1 1 0 0 1 1 1V20a1 1 0 0 1-1 1A17 17 0 0 1 3 4a1 1 0 0 1 1-1h3.5a1 1 0 0 1 1 1c0 1.25.2 2.45.57 3.6a1 1 0 0 1-.25 1z"/></svg>
            022 418 57 34
          </span>
          <span class="contact__item">
            <svg class="icon" viewBox="0 0 24 24"><path d="M2 5h20v14H2z" fill="none" stroke="#2b93d9" stroke-width="2"/><path d="M2 5l10 8 10-8" fill="none" stroke="#2b93d9" stroke-width="2"/></svg>
            tv@clairevalconseil.ch
          </span>
          <span class="contact__item">
            <svg class="icon" viewBox="0 0 24 24"><circle cx="12" cy="12" r="10" fill="none" stroke="#2b93d9" stroke-width="2"/><path d="M2 12h20M12 2c3 3 3 17 0 20M12 2c-3 3-3 17 0 20" fill="none" stroke="#2b93d9" stroke-width="2"/></svg>
            www.clairevalconseil.ch
          </span>
        </div>
        <div class="contact__row">
          <span class="contact__item">
            <svg class="icon" viewBox="0 0 24 24"><path d="M12 2a7 7 0 0 0-7 7c0 5 7 13 7 13s7-8 7-13a7 7 0 0 0-7-7zm0 9.5A2.5 2.5 0 1 1 12 6.5a2.5 2.5 0 0 1 0 5z"/></svg>
            Rue des Vergières 27 1201 Genève
          </span>
        </div>
      </div>
    </div>
    <div class="brand">
      <span class="brand__mark"></span>
      <div>
        <div class="brand__name">Claireval</div>
        <div class="brand__sub">Conseil et Comptes</div>
      </div>
    </div>
    <div class="card__band"></div>
  </section>
</body>
</html>
```